New Business Card Design Project

We require a business card design for Vexalund, a newly established Indian company.
Our focus is on the development, manufacturing, and export of a diverse array of pharmaceutical products on a global scale. The card should convey a professional appearance, as our primary markets are in Africa, China, and Southeast Asian nations.
We envision a two-sided business card, with the reverse side dedicated to a logo set against a solid color or an elegantly designed pattern. The corners should be rounded. We would appreciate seeing both horizontal and vertical design options. We trust the designer to utilize their expertise in creating this design.

The content for the business card is included in the attached Word file.

Target Market(s)

Our primary markets are in Africa, China, and Southeast Asian, Latin America, Maldives, Sri Lanka

Industry/Entity Type

Pharmaceutical Manufacturing and Export

Contact Information for Business Card

Colors

Designer to choose colors to be used in the design.

Requirements
Must have
• The reverse side of the business card features solely the logo along with the tagline, "Care Beyond Borders."
Should not have
• The logo should not exceed two instances, encompassing both the front and back sides of the card.

```html
<!DOCTYPE html>
<html lang="en">
<head>
<meta charset="utf-8">
<title>Vexalund Business Card</title>
<link rel="stylesheet" href="https://fonts.googleapis.com/css2?family=Montserrat:wght@400;600;700&family=Open+Sans:wght@400;600&display=swap">
<style>
  :root{
    --bg:#ecdccb;
    --card:#ffffff;
    --blue:#2ea6df;
    --red:#f0614d;
    --ink:#1d1d1f;
    --shadow:rgba(90,60,40,.25);
  }
  *{box-sizing:border-box;margin:0;padding:0}
  html,body{width:1200px;height:711px;overflow:hidden;background:var(--bg)}
  .stage{position:relative;width:1200px;height:711px}
  .card{
    position:absolute;top:207px;width:520px;height:297px;
    background:var(--card);border-radius:18px;overflow:hidden;
    box-shadow:0 14px 30px var(--shadow);
  }
  .card--back{left:50px}
  .card--front{left:630px}

  .brand{display:flex;align-items:center;gap:10px;font-family:"Montserrat",sans-serif;font-weight:700;color:var(--blue);letter-spacing:.5px;white-space:nowrap}
  .brand__dot{border-radius:50%;background:var(--red);flex:none}

  .card--back .brand{position:absolute;left:0;right:0;top:100px;justify-content:center;font-size:60px}
  .card--back .brand__dot{width:26px;height:26px}
  .tagline{position:absolute;right:92px;top:190px;font-family:"Montserrat",sans-serif;font-size:15px;color:var(--ink);letter-spacing:.3px;white-space:nowrap}

  .card--front .brand{position:absolute;left:24px;top:104px;font-size:38px;gap:8px}
  .card--front .brand__dot{width:16px;height:16px}
  .divider{position:absolute;left:268px;top:40px;width:1px;height:170px;background:var(--blue)}

  .person{position:absolute;left:290px;top:44px}
  .person__name{font-family:"Montserrat",sans-serif;font-size:20px;line-height:1.1;white-space:nowrap}
  .person__first{color:var(--blue);font-weight:700}
  .person__last{color:var(--red);font-weight:400}
  .person__role{font-family:"Montserrat",sans-serif;font-size:13px;color:var(--ink);margin-top:4px}

  .contacts{position:absolute;left:290px;top:120px;list-style:none;font-family:"Open Sans",sans-serif;font-size:12.5px;color:var(--ink)}
  .contacts li{display:flex;align-items:center;gap:8px;height:22px;white-space:nowrap}
  .contacts svg{width:13px;height:13px;flex:none}

  .band{position:absolute;bottom:22px;height:28px}
  .band--address{left:0;width:420px;background:var(--blue);color:#fff;font-family:"Open Sans",sans-serif;font-size:13px;display:flex;align-items:center;padding-left:22px;letter-spacing:.2px;white-space:nowrap}
  .band--accent{left:420px;right:0;background:var(--red)}
</style>
</head>
<body>
<main class="stage">
  <section class="card card--back" aria-label="Card reverse">
    <div class="brand"><span class="brand__dot"></span>Vexalund</div>
    <p class="tagline">Care Beyond Borders.</p>
  </section>

  <section class="card card--front" aria-label="Card front">
    <div class="brand"><span class="brand__dot"></span>Vexalund</div>
    <span class="divider"></span>
    <div class="person">
      <p class="person__name"><span class="person__first">Rohan</span> <span class="person__last">K. Deshmane</span></p>
      <p class="person__role">CEO</p>
    </div>
    <ul class="contacts">
      <li>
        <svg viewBox="0 0 14 14"><rect x="3" y="1" width="8" height="12" rx="1.5" fill="none" stroke="var(--red)" stroke-width="1.6"/></svg>
        +919 555014260
      </li>
      <li>
        <svg viewBox="0 0 14 14"><circle cx="7" cy="7" r="6" fill="none" stroke="var(--blue)" stroke-width="1.4"/><ellipse cx="7" cy="7" rx="2.6" ry="6" fill="none" stroke="var(--blue)" stroke-width="1.2"/><line x1="1" y1="7" x2="13" y2="7" stroke="var(--blue)" stroke-width="1.2"/></svg>
        www.vexalund.com
      </li>
      <li>
        <svg viewBox="0 0 14 14"><rect x="1" y="3" width="12" height="9" rx="1" fill="var(--red)"/><polyline points="1.5,3.5 7,8 12.5,3.5" fill="none" stroke="#fff" stroke-width="1.2"/></svg>
        rdeshmane@vexalund.com
      </li>
    </ul>
    <div class="band band--address">7, Kamalvan Colony, Ranpur, 445990, India</div>
    <div class="band band--accent"></div>
  </section>
</main>
</body>
</html>
```